Verodex business card

Business card for sustainable investment company called "Verodex". Verodex is an exchange platform selling carbon credits between buyers and sellers. Carbon Credits are an environmental commodity for reducing global carbon emissions.

the card should obviously have our logo and the theme should be sustainability/environment mixed with a trading platform.

Contact Information for Business Card

Logo, Name, Title, Phone, Email

Colors
0054AA
0677BA
7BADD7
CADEEF
E8F1F8
0094D4
00A9DD
6FCCEA
C7EBF8
E9F6FB
00AB8E
00BBA5
67D7C9
C6EFE9
E9F9F6
59FF00
82FF00
B8FF75
E3FFCB
F4FFEA

```html
<!DOCTYPE html>
<html lang="en">
<head>
<meta charset="utf-8">
<title>Verodex business card</title>
<link href="https://fonts.googleapis.com/css2?family=Poppins:wght@400;500;600;700&display=swap" rel="stylesheet">
<style>
  :root {
    --stage: #2a2b2d;
    --paper: #ffffff;
    --navy: #1c2b4b;
    --ink-soft: #2c3a58;
    --rule: #3a4660;
    --cyan: #33e2ec;
    --blue: #1f78e6;
    --mid-blue: #2aa6e9;
  }
  * { box-sizing: border-box; margin: 0; padding: 0; }
  html, body {
    width: 1200px; height: 866px; overflow: hidden;
    background: var(--stage);
    font-family: "Poppins", sans-serif;
  }
  .stage {
    position: relative; width: 1200px; height: 866px;
    display: flex; flex-direction: column; align-items: center; justify-content: center; gap: 46px;
  }
  .card {
    position: relative; width: 560px; height: 320px; overflow: hidden;
    box-shadow: 0 14px 30px rgba(0,0,0,.45);
  }
  .card-front { background: var(--paper); color: var(--navy); }
  .card-back {
    background: linear-gradient(135deg, var(--cyan) 0%, var(--mid-blue) 45%, var(--blue) 100%);
    display: flex; align-items: center; justify-content: center;
  }
  .brand { display: flex; align-items: center; gap: 14px; }
  .brand-mark { width: 34px; height: 34px; background: var(--blue); border-radius: 4px; }
  .brand-name {
    font-weight: 600; font-size: 40px; letter-spacing: 4px; text-transform: uppercase; line-height: 1;
  }
  .card-front .brand { position: absolute; left: 236px; top: 86px; }
  .card-front .brand-name { color: var(--navy); }
  .card-back .brand-mark { background: #ffffff; }
  .card-back .brand-name { color: #ffffff; }
  .holder { position: absolute; left: 34px; top: 168px; }
  .holder-name { font-weight: 700; font-size: 16px; letter-spacing: 1.5px; text-transform: uppercase; }
  .holder-title { font-size: 12.5px; color: var(--ink-soft); margin-top: 1px; }
  .title-rule {
    position: absolute; left: 176px; top: 206px; width: 350px; height: 1px; background: var(--rule);
  }
  .contact { position: absolute; left: 34px; top: 222px; font-size: 12.5px; line-height: 20px; color: var(--navy); }
  .contact-row { display: flex; align-items: center; gap: 8px; }
  .contact-row svg { width: 13px; height: 13px; flex: none; }
  .footer-band { position: absolute; left: 0; bottom: 0; width: 560px; height: 60px; }
  .website {
    position: absolute; right: 30px; bottom: 12px; font-size: 13px; letter-spacing: .5px; color: #ffffff;
  }
</style>
</head>
<body>
<main class="stage">
  <section class="card card-front">
    <div class="brand">
      <span class="brand-mark"></span>
      <span class="brand-name">Verodex</span>
    </div>
    <div class="holder">
      <p class="holder-name">Daniel Harper</p>
      <p class="holder-title">Managing Director</p>
    </div>
    <div class="title-rule"></div>
    <div class="contact">
      <p class="contact-row">
        <svg viewBox="0 0 16 16"><path d="M4 1.5l2.3 2.6-1.3 1.6c.9 2 2.6 3.6 4.6 4.6l1.6-1.3 2.6 2.3-1.4 2.5C7.6 13.5 2.5 8.4 1.5 3z" fill="var(--mid-blue)"/></svg>
        044-987 654 321
      </p>
      <p class="contact-row">
        <svg viewBox="0 0 16 16"><rect x="1" y="3.5" width="14" height="9" rx="1" fill="var(--mid-blue)"/><path d="M1.5 4l6.5 5 6.5-5" fill="none" stroke="#fff" stroke-width="1.2"/></svg>
        hello@verodexmail.com
      </p>
    </div>
    <svg class="footer-band" viewBox="0 0 560 60" preserveAspectRatio="none">
      <defs>
        <linearGradient id="stripe" x1="0" x2="1" y1="0" y2="0">
          <stop offset="0" stop-color="var(--cyan)"/>
          <stop offset="1" stop-color="var(--blue)"/>
        </linearGradient>
      </defs>
      <path d="M0 48 L210 48 L210 54 L0 54 Z" fill="url(#stripe)"/>
      <path d="M200 60 C222 60 222 30 252 30 L560 30 L560 60 Z" fill="var(--navy)"/>
    </svg>
    <p class="website">www.verodexsite.com</p>
  </section>

  <section class="card card-back">
    <div class="brand">
      <span class="brand-mark"></span>
      <span class="brand-name">Verodex</span>
    </div>
  </section>
</main>
</body>
</html>
```